Corvane Capital Business Cards

These are professional business cards that are for my family office.
Put fake emails and phone numbers as of now until I finalize those components. This family office controls my families investments, assets, and future. The cards should be professional.
..
.
.
.
I just uploaded another variation of a logo I would like to see as a business card to I am inbeteen which logo to use

Target Market(s)

business

Industry/Entity Type

business

Contact Information for Business Card

Professional, wealth related, finance related.

Requirements
Must have
• Logo

```html
<!DOCTYPE html>
<html lang="en">
<head>
<meta charset="utf-8">
<title>Corvane Capital Business Cards</title>
<link rel="stylesheet" href="https://fonts.googleapis.com/css2?family=Montserrat:wght@400;700&display=swap">
<style>
  :root {
    --backdrop: #e9e6e1;
    --card: #ffffff;
    --ink: #1c2033;
    --muted: #9a9a9a;
    --shadow: rgba(40, 30, 20, 0.28);
  }
  * { margin: 0; padding: 0; box-sizing: border-box; }
  html, body { width: 1200px; height: 931px; overflow: hidden; }
  body {
    background: var(--backdrop);
    font-family: "Montserrat", sans-serif;
    color: var(--ink);
    position: relative;
  }
  .card {
    position: absolute;
    width: 580px;
    height: 331px;
    background: var(--card);
    border-radius: 22px;
    box-shadow: 0 14px 30px var(--shadow);
  }
  .card--front { left: 50px; top: 70px; }
  .card--back { left: 570px; top: 520px; }

  .brand {
    display: flex;
    align-items: center;
    gap: 16px;
    text-transform: uppercase;
    font-weight: 700;
    letter-spacing: 0.12em;
    color: var(--ink);
  }
  .brand__dot {
    border: 3px solid var(--ink);
    border-radius: 50%;
    flex: none;
  }
  .card--front .brand {
    position: absolute;
    left: 0; right: 0; top: 0; bottom: 0;
    flex-direction: column;
    justify-content: center;
    font-size: 30px;
  }
  .card--front .brand__dot { width: 120px; height: 120px; }

  .card--back .brand {
    position: absolute;
    right: 40px;
    top: 34px;
    flex-direction: column;
    font-size: 17px;
    gap: 12px;
  }
  .card--back .brand__dot { width: 70px; height: 70px; border-width: 2px; }

  .divider {
    position: absolute;
    left: 40px; right: 40px;
    top: 168px;
    height: 2px;
    background: var(--ink);
  }
  .address {
    position: absolute;
    right: 40px;
    top: 186px;
    text-align: right;
    font-size: 12px;
    line-height: 1.45;
  }
  .person {
    position: absolute;
    left: 40px;
    top: 126px;
  }
  .person__name { font-size: 28px; font-weight: 700; line-height: 1; }
  .person__role { font-size: 13px; margin-top: 52px; }
  .person__rule { width: 150px; height: 2px; background: var(--ink); margin: 8px 0 10px; }
  .contact { list-style: none; font-size: 14px; }
  .contact li { display: flex; align-items: center; gap: 10px; margin-bottom: 7px; }
  .contact svg { width: 14px; height: 14px; fill: var(--ink); flex: none; }
</style>
</head>
<body>
  <section class="card card--front">
    <div class="brand">
      <span class="brand__dot"></span>
      <span class="brand__name">Corvane Capital</span>
    </div>
  </section>

  <section class="card card--back">
    <div class="brand">
      <span class="brand__dot"></span>
      <span class="brand__name">Corvane Capital</span>
    </div>
    <div class="divider"></div>
    <address class="address" style="font-style:normal">
      240 Harbor View Plaza<br>
      Brookfield, NJ 07010 USA
    </address>
    <div class="person">
      <div class="person__name">Marcus Delgado</div>
      <div class="person__role">Owner</div>
      <div class="person__rule"></div>
      <ul class="contact">
        <li>
          <svg viewBox="0 0 24 24"><path d="M6.6 10.8a15.1 15.1 0 0 0 6.6 6.6l2.2-2.2a1 1 0 0 1 1-.25 11.4 11.4 0 0 0 3.6.57 1 1 0 0 1 1 1V20a1 1 0 0 1-1 1A17 17 0 0 1 3 4a1 1 0 0 1 1-1h3.5a1 1 0 0 1 1 1c0 1.25.2 2.45.57 3.6a1 1 0 0 1-.25 1z"/></svg>
          (555)014-2786
        </li>
        <li>
          <svg viewBox="0 0 24 24"><path d="M2 5h20v14H2z M2 5l10 8 10-8" /></svg>
          info@yourwebsitename.com
        </li>
        <li>
          <svg viewBox="0 0 24 24"><circle cx="12" cy="12" r="10"/></svg>
          www.yourwebsitename.com
        </li>
      </ul>
    </div>
  </section>
</body>
</html>
```